LM-Steuerberatung WordPress Site fully implemented (tax advisor)

Hello!
I need a little Wordpress Site for my newly founded Tax-Advisor Company.
I am a one-man Office advising in the area of Crypto-Currency.
PLEASE only provide a Design, if you can also Implement a WP-Site afterwards on an existing Webspace.

Please find the Content and Website-Description in the attached Document

Language for the Website is German (for now)

Target Market(s)

Tax-Advisory (specialized in Crypto Currency)

Coding

Coded - Design and coding required

Number of Pages Required

5+ page

Font styles to use
Sans Serif

Requirements
Must have
• Wordpress Implementation afterwards - Details according to attached Project Information Document

```html
<!DOCTYPE html>
<html lang="de">
<head>
<meta charset="utf-8">
<title>LM-Steuerberatung</title>
<link href="https://fonts.googleapis.com/css2?family=Roboto:wght@400;500;700&family=Roboto+Condensed:wght@400;700&display=swap" rel="stylesheet">
<style>
  :root {
    --navy: #1c2a44;
    --navy-deep: #05070d;
    --white: #ffffff;
    --nav-grey: #9aa0a8;
    --nav-active: #1c2a44;
  }
  * { box-sizing: border-box; margin: 0; padding: 0; }
  html, body { width: 1200px; height: 790px; overflow: hidden; background: var(--white); }
  body { position: relative; font-family: "Roboto Condensed", "Roboto", sans-serif; color: var(--white); }

  .site-header { position: absolute; top: 0; left: 0; width: 1200px; height: 81px; background: var(--white); }
  .brand { position: absolute; left: 99px; top: 27px; display: flex; align-items: center; gap: 10px;
    font-family: "Roboto", sans-serif; font-weight: 700; font-size: 19px; letter-spacing: 0.5px; color: var(--navy); }
  .brand-mark { width: 26px; height: 26px; background: var(--navy); }
  .main-nav { position: absolute; top: 0; left: 0; font-family: "Roboto", sans-serif; font-size: 16px; }
  .nav-item { position: absolute; top: 31px; color: var(--nav-grey); white-space: nowrap; }
  .nav-item.is-active { color: var(--nav-active); }
  .nav-active-bar { position: absolute; top: 0; left: 511px; width: 54px; height: 3px; background: var(--navy); }

  .hero { position: absolute; top: 81px; left: 0; width: 1200px; height: 658px;
    background:
      radial-gradient(ellipse 420px 320px at 1000px 470px, rgba(150,175,215,0.55), transparent 70%),
      radial-gradient(ellipse 500px 400px at 780px 150px, rgba(110,135,180,0.45), transparent 70%),
      linear-gradient(90deg, var(--navy-deep) 0%, #0b1220 40%, #2a3a58 70%, #4a5d80 100%); }
  .hero-content { position: absolute; left: 99px; top: 0; }
  .hero-kicker { position: absolute; top: 111px; left: 0; font-weight: 700; font-size: 52px; white-space: nowrap; line-height: 1; }
  .hero-title { position: absolute; top: 172px; left: 0; font-weight: 700; font-size: 70px; white-space: nowrap; line-height: 1; }
  .hero-lead { position: absolute; top: 270px; left: 0; width: 560px; font-size: 18px; line-height: 26px; }
  .hero-button { position: absolute; top: 357px; left: -3px; width: 281px; height: 57px; border-radius: 16px;
    background: var(--navy); display: flex; align-items: center; justify-content: center;
    font-size: 16.5px; font-weight: 700; }
  .quotes-title { position: absolute; top: 450px; left: 0; font-size: 26px; font-weight: 700; white-space: nowrap; }
  .quote-list { position: absolute; top: 510px; left: 0; list-style: none; }
  .quote-list li { display: flex; align-items: center; gap: 17px; height: 33.5px; font-size: 17.5px; white-space: nowrap; }
  .quote-list svg { width: 14px; height: 14px; flex: none; }

  .site-footer { position: absolute; top: 739px; left: 0; width: 1200px; height: 51px; background: var(--navy);
    font-family: "Roboto Condensed", sans-serif; font-size: 16.5px; }
  .copyright { position: absolute; left: 98px; top: 15px; white-space: nowrap; }
  .social { position: absolute; left: 866px; top: 15px; display: flex; align-items: center; gap: 16px; white-space: nowrap; }
  .social-dot { width: 17px; height: 17px; border-radius: 50%; background: var(--white); }
</style>
</head>
<body>
  <header class="site-header">
    <div class="brand"><span class="brand-mark"></span>LM STEUERBERATUNG</div>
    <nav class="main-nav">
      <span class="nav-active-bar"></span>
      <span class="nav-item is-active" style="left:518px">Home</span>
      <span class="nav-item" style="left:614px">Leistungen ⌄</span>
      <span class="nav-item" style="left:760px">Über mich</span>
      <span class="nav-item" style="left:885px">Kontakt</span>
      <span class="nav-item" style="left:998px">Impressum</span>
    </nav>
  </header>

  <section class="hero" role="img" aria-label="Hintergrundbild: Hand an einem Laptop mit leuchtenden Netzwerkstrukturen und Binärzahlen in Blautönen">
    <div class="hero-content">
      <h2 class="hero-kicker">WILLKOMMEN BEI</h2>
      <h1 class="hero-title">LM-STEUERBERATUNG!</h1>
      <p class="hero-lead">Ihrem Spezialisten bei allen steuerlichen Themen rund um Einkünfte &amp;amp; Vermögen aus Krypto-Assets.</p>
      <a class="hero-button">Weiter zu unseren Leistungen</a>
      <h3 class="quotes-title">Quotations:</h3>
      <ul class="quote-list">
        <li><svg viewBox="0 0 14 14"><circle cx="7" cy="7" r="7" fill="#fff"/><path d="M3.8 7.2l2.2 2.1 4.2-4.3" stroke="#0b1220" stroke-width="1.8" fill="none"/></svg>Dann mach ich eine Schweizer Holding-Gesellschaft– dort zahlt man fast keine Steuern</li>
        <li><svg viewBox="0 0 14 14"><circle cx="7" cy="7" r="7" fill="#fff"/><path d="M3.8 7.2l2.2 2.1 4.2-4.3" stroke="#0b1220" stroke-width="1.8" fill="none"/></svg>dann melde ich einfach meinen Hauptwohnsitz in Österreich ab</li>
        <li><svg viewBox="0 0 14 14"><circle cx="7" cy="7" r="7" fill="#fff"/><path d="M3.8 7.2l2.2 2.1 4.2-4.3" stroke="#0b1220" stroke-width="1.8" fill="none"/></svg>Dann lass ich meine Kryptos auf einer Börse in Singapur, dort ist das steuerfrei</li>
      </ul>
    </div>
  </section>

  <footer class="site-footer">
    <p class="copyright">© copyrights 2022&nbsp;&nbsp; LM-Steuerberatung |&nbsp; All Rights Reserved</p>
    <div class="social">Social Media :
      <span class="social-dot" aria-label="Social-Media-Link"></span>
      <span class="social-dot" aria-label="Social-Media-Link"></span>
      <span class="social-dot" aria-label="Social-Media-Link"></span>
      <span class="social-dot" aria-label="Social-Media-Link"></span>
    </div>
  </footer>
</body>
</html>
```